Diverse, up-scale salon needs eye-catching, unique business cards.

We are looking for a unique business card design for our stylist but that can also be multi functional and used for appointment reminder and referrals. I will need a design in a format that I can modify names and titles going forward. In the past we have had a dark background with the logo on one side, and stylist and contact information on the other but we are open to all ideas. I have included our mission statement as well as branded colors below. The statement doesn't need to go on the card, it's just a reference for target market. We need space for the stylists name, title, instagram handle and then the salons phone number, website and address. I am also open to adding a spot for a qr code linked to the stylist instagram or the salon booking link.

primary brand colors:
#333333 #233415 #36502a #93874a #000000
Mission statement:
Vessolin Hair Studio, a high-end salon located in the lively Downtown Farmington, Michigan, is committed to providing exceptional services in a welcoming and relaxed environment to meet the needs of our diverse clientele.
Our salon specializes in contemporary custom haircuts, coloring, extensions, and barbering and beard grooming services. Our team of skilled stylists is passionate and inventive in their hair styling techniques. At the heart of our salon are values centered on quality, innovation, creativity, and above all, comfort. These core values are evident in every appointment across our customizable array of services.
Our goal is to establish a benchmark for exceptional hair care for every human.
Website: www.vessolinhairstudio.example
instagram: @vessolinhairstudio
address: 41782 Pelham Crest Rd, Farmington MI
phone: 248-613-4087

Industry/Entity Type

Hair Salon

Contact Information for Business Card

Stylist name, title, phone, instagram, website, address, (optional qr code)

Requirements
Should not have
• Does not need mission statement on the card.

```html
<!DOCTYPE html>
<html lang="en">
<head>
<meta charset="UTF-8">
<title>Vessolin Hair Studio — Business Card</title>
<link href="https://fonts.googleapis.com/css2?family=Montserrat:wght@500;600&display=swap" rel="stylesheet">
<style>
  :root {
    --olive: #93874a;
    --forest: #233415;
    --charcoal: #333333;
    --ink: #000000;
    --paper: #ffffff;
    --backdrop: #e3e3e1;
  }
  html, body {
    margin: 0;
    padding: 0;
    width: 1200px;
    height: 900px;
    overflow: hidden;
    background: var(--backdrop);
    font-family: "Montserrat", Arial, sans-serif;
  }
  .canvas {
    position: relative;
    width: 1200px;
    height: 900px;
  }
  .card {
    position: absolute;
    width: 540px;
    height: 309px;
    box-shadow: 0 14px 30px rgba(0,0,0,0.18);
    overflow: hidden;
  }
  .card-front {
    left: 50px;
    top: 150px;
    background: var(--olive);
    display: flex;
    align-items: center;
    justify-content: center;
  }
  .brand-name {
    font-weight: 600;
    letter-spacing: 0.14em;
    text-transform: uppercase;
    text-align: center;
    line-height: 1.35;
    margin: 0;
  }
  .card-front .brand-name {
    color: var(--paper);
    font-size: 26px;
  }
  .card-back {
    left: 610px;
    top: 440px;
    background: var(--paper);
  }
  .card-back .swoosh {
    position: absolute;
    left: 0;
    top: 0;
    width: 540px;
    height: 309px;
  }
  .card-back .brand-name {
    position: absolute;
    left: 40px;
    top: 98px;
    width: 175px;
    color: var(--olive);
    font-size: 16px;
  }
  .divider {
    position: absolute;
    left: 236px;
    top: 62px;
    width: 2px;
    height: 126px;
    background: var(--olive);
  }
  .contact {
    position: absolute;
    left: 254px;
    top: 60px;
    color: var(--ink);
    font-weight: 500;
    font-size: 12.5px;
    line-height: 1.35;
  }
  .contact .address { margin: 0 0 12px; }
  .contact ul { list-style: none; margin: 0; padding: 0; }
  .contact li {
    display: flex;
    align-items: center;
    gap: 6px;
    margin-bottom: 3px;
  }
  .contact svg { width: 12px; height: 12px; flex: none; }
</style>
</head>
<body>
<main class="canvas">
  <section class="card card-front">
    <p class="brand-name">Vessolin<br>Hair Studio</p>
  </section>

  <section class="card card-back">
    <svg class="swoosh" viewBox="0 0 540 309" aria-hidden="true">
      <path d="M250 240 C370 210 470 160 540 105 L540 140 C460 182 360 222 250 240 Z" fill="var(--forest)"/>
      <path d="M0 232 C200 226 400 192 540 128 L540 150 C400 205 200 246 0 268 Z" fill="var(--charcoal)"/>
      <path d="M0 262 C200 246 400 202 540 142 L540 309 L0 309 Z" fill="var(--olive)"/>
    </svg>

    <p class="brand-name">Vessolin<br>Hair Studio</p>
    <div class="divider"></div>

    <div class="contact">
      <p class="address">41782 Pelham Crest Rd,<br>Farmington MI</p>
      <ul>
        <li>
          <svg viewBox="0 0 12 12" aria-hidden="true"><path d="M2.5 1 L4.5 1 L5.2 3.6 L4 4.6 C4.6 5.9 6 7.4 7.4 8 L8.4 6.8 L11 7.5 L11 9.5 C11 10.3 10.3 11 9.5 11 C5 11 1 7 1 2.5 C1 1.7 1.7 1 2.5 1 Z" fill="var(--charcoal)"/></svg>
          <span>248-613-4087</span>
        </li>
        <li>
          <svg viewBox="0 0 12 12" aria-hidden="true"><circle cx="6" cy="6" r="5" fill="none" stroke="var(--charcoal)" stroke-width="1.2"/><path d="M1 6 H11 M6 1 C3.5 4 3.5 8 6 11 M6 1 C8.5 4 8.5 8 6 11" fill="none" stroke="var(--charcoal)" stroke-width="1"/></svg>
          <span>www.vessolinhairstudio.example</span>
        </li>
        <li>
          <svg viewBox="0 0 12 12" aria-hidden="true"><rect x="1" y="1" width="10" height="10" rx="2" fill="none" stroke="var(--charcoal)" stroke-width="1.3"/></svg>
          <span>@vessolinhairstudio</span>
        </li>
      </ul>
    </div>
  </section>
</main>
</body>
</html>
```